Homemaking training schools needs a Business Card design

Designer, Hello!

No special requirements, good-looking enough.
--------------------------------------------------------------------------

Name: Marcus Dole
Chairman
Tel: 0574-71948263
Mobile: 13857420916
Email: kelvora@mailnest.example
Web: www.prt2019.example
Add: No.258, LanpingJie, BeiyuanQu, Ningbo, Zhejiang

LOGO
Ningbo PRT Homemaking Training School

Target Market(s)

pregnant women, mothers, infants, the elderly and families, including cleaning, cooking, nursing training.

Industry/Entity Type

Business

Contact Information for Business Card

Name: Marcus Dole
Chairman
Tel: 0574-71948263
Mobile: 13857420916
Email: kelvora@mailnest.example
Web: www.prt2019.example

LOGO

Font styles to use
Serif
Sans Serif
Decorative

Requirements
Nice to have
• Feels: clean, specifications, safety, comfort, warmth and happiness.

```html
<!DOCTYPE html>
<html lang="en">
<head>
<meta charset="utf-8">
<title>PinRuiTang Business Card</title>
<link href="https://fonts.googleapis.com/css2?family=Raleway:wght@400;500;700&display=swap" rel="stylesheet">
<style>
  :root {
    --backdrop: #bfe3d9;
    --card: #ffffff;
    --ink: #1d1d1f;
    --brand-blue: #0a6ab8;
    --brand-pink: #e6007e;
    --soft-blue: #c9d4ee;
    --mid-blue: #a9bbe4;
  }
  * { box-sizing: border-box; margin: 0; padding: 0; }
  html, body { width: 1200px; height: 856px; overflow: hidden; }
  body {
    background: var(--backdrop);
    font-family: "Raleway", sans-serif;
    color: var(--ink);
    position: relative;
  }
  .card {
    position: absolute;
    width: 640px;
    height: 366px;
    background: var(--card);
    border-radius: 26px;
    overflow: hidden;
    box-shadow: 0 10px 28px rgba(40, 90, 80, 0.18);
  }
  .card-back { left: 500px; top: 40px; }
  .card-front { left: 60px; top: 450px; }

  .card-art { position: absolute; inset: 0; width: 100%; height: 100%; }

  .edge-band {
    position: absolute;
    top: 0; bottom: 0;
    width: 30px;
    background: var(--brand-blue);
  }
  .edge-band::after {
    content: "";
    position: absolute;
    top: 0; bottom: 0;
    width: 6px;
    background: var(--brand-pink);
  }
  .edge-band-left { left: 0; }
  .edge-band-left::after { right: -12px; }
  .edge-band-right { right: 0; }
  .edge-band-right::after { left: -12px; }

  .wordmark {
    position: absolute;
    display: flex;
    align-items: center;
    gap: 8px;
    font-weight: 700;
    color: var(--brand-blue);
    letter-spacing: 0.5px;
  }
  .wordmark-dot {
    width: 12px; height: 12px;
    border-radius: 50%;
    background: var(--brand-pink);
  }
  .card-back .wordmark { left: 0; right: 0; top: 158px; justify-content: center; font-size: 38px; }
  .card-front .wordmark { left: 150px; top: 298px; font-size: 30px; }

  .holder { position: absolute; left: 44px; top: 40px; }
  .holder-name {
    font-size: 31px;
    font-weight: 500;
    text-transform: uppercase;
    letter-spacing: 1px;
    line-height: 1.1;
  }
  .holder-title { font-size: 21px; color: var(--brand-blue); font-weight: 500; }

  .contact-list { list-style: none; margin-top: 10px; }
  .contact-item {
    display: flex;
    align-items: center;
    gap: 12px;
    font-size: 17px;
    line-height: 25px;
    letter-spacing: 0.4px;
  }
  .contact-icon { width: 18px; height: 18px; flex: none; }

  .address-band {
    position: absolute;
    left: 0; right: 0; top: 250px;
    height: 32px;
    background: var(--brand-blue);
    color: #fff;
    font-size: 16px;
    line-height: 32px;
    padding-left: 110px;
    letter-spacing: 0.4px;
  }
</style>
</head>
<body>

  <section class="card card-back" aria-label="Business card, back">
    <div class="edge-band edge-band-left" aria-hidden="true"></div>
    <div class="edge-band edge-band-right" aria-hidden="true"></div>
    <div class="wordmark"><span class="wordmark-dot"></span>PinRuiTang</div>
  </section>

  <section class="card card-front" aria-label="Business card, front">
    <svg class="card-art" viewBox="0 0 640 366" aria-hidden="true">
      <circle cx="560" cy="80" r="190" fill="var(--soft-blue)" opacity="0.7"/>
      <circle cx="600" cy="330" r="210" fill="var(--soft-blue)" opacity="0.75"/>
      <circle cx="640" cy="380" r="170" fill="var(--mid-blue)" opacity="0.6"/>
    </svg>

    <div class="holder">
      <h1 class="holder-name">Marcus Dole</h1>
      <p class="holder-title">Chairman</p>
      <ul class="contact-list">
        <li class="contact-item">
          <svg class="contact-icon" viewBox="0 0 20 20" aria-hidden="true"><circle cx="10" cy="10" r="8.5" fill="none" stroke="var(--brand-blue)" stroke-width="1.6"/><path d="M7 6l2 2-1 1.5c.7 1.3 1.6 2.2 2.8 2.8L12 11l2 2-1.2 1.2C9.5 14 6 10.5 5.8 7.2z" fill="var(--brand-blue)"/></svg>
          0574-71948263
        </li>
        <li class="contact-item">
          <svg class="contact-icon" viewBox="0 0 20 20" aria-hidden="true"><circle cx="10" cy="10" r="8.5" fill="none" stroke="var(--brand-blue)" stroke-width="1.6"/><rect x="7" y="5" width="6" height="10" rx="1" fill="none" stroke="var(--brand-blue)" stroke-width="1.4"/></svg>
          13857420916
        </li>
        <li class="contact-item">
          <svg class="contact-icon" viewBox="0 0 20 20" aria-hidden="true"><rect x="2" y="5" width="16" height="11" fill="none" stroke="var(--brand-blue)" stroke-width="1.6"/><path d="M2 5l8 6 8-6" fill="none" stroke="var(--brand-blue)" stroke-width="1.6"/></svg>
          kelvora@mailnest.example
        </li>
        <li class="contact-item">
          <svg class="contact-icon" viewBox="0 0 20 20" aria-hidden="true"><circle cx="10" cy="10" r="8.5" fill="var(--brand-blue)"/><path d="M1.5 10h17M10 1.5c-3 3-3 14 0 17M10 1.5c3 3 3 14 0 17" fill="none" stroke="#fff" stroke-width="1.2"/></svg>
          www.prt2019.example
        </li>
      </ul>
    </div>

    <p class="address-band">No.258, LanpingJie, BeiyuanQu, Ningbo, Zhejiang</p>

    <div class="wordmark"><span class="wordmark-dot"></span>PinRuiTang</div>
  </section>

</body>
</html>
```